"Harbor Builders" is a residential building company and needs a new business card design and may re

We would like a redesign based on the existing logo, and would like to see a new font as well. We are bespoke home builders who build sustainable energy efficient homes.

Industry/Entity Type

Construction

Contact Information for Business Card

Business card size 40mm x 90mm

Colors

Designer to choose colors to be used in the design.

```html
<!DOCTYPE html>
<html lang="en">
<head>
<meta charset="utf-8">
<title>Harbor Builders – Business Card</title>
<link rel="stylesheet" href="https://fonts.googleapis.com/css2?family=Open+Sans:wght@400;600;700&family=Roboto+Condensed:wght@700&display=swap">
<style>
  :root {
    --stage: #d9d4cc;
    --card-white: #f6f6f4;
    --brand-green: #bcd631;
    --ink: #1c1c1c;
    --text-grey: #4a4a4a;
    --white: #ffffff;
  }
  * { box-sizing: border-box; margin: 0; padding: 0; }
  html, body {
    width: 1200px; height: 960px; overflow: hidden;
    background: var(--stage);
    font-family: "Open Sans", Arial, sans-serif;
  }
  .canvas { position: relative; width: 1200px; height: 960px; }

  .card { position: absolute; width: 601px; height: 342px; }
  .card--front { left: 302px; top: 129px; background: var(--card-white); }
  .card--back { left: 299px; top: 489px; background: var(--brand-green); }

  .brand {
    position: absolute; right: 32px; top: 52px;
    display: flex; align-items: center; gap: 12px;
  }
  .brand__square { width: 22px; height: 22px; background: var(--brand-green); }
  .brand__name {
    font-family: "Open Sans", Arial, sans-serif; font-weight: 600;
    font-size: 30px; color: var(--ink); letter-spacing: -0.5px;
  }

  .holder {
    position: absolute; left: 28px; top: 164px;
    font-family: "Roboto Condensed", "Arial Narrow", sans-serif;
    font-weight: 700; font-size: 22px; color: var(--ink);
  }
  .rule {
    position: absolute; left: 30px; top: 196px; width: 538px; height: 3px;
    background: linear-gradient(to right, var(--brand-green) 0 50%, var(--ink) 50% 100%);
  }

  .details {
    position: absolute; left: 30px; top: 206px;
    font-size: 14px; line-height: 19px; color: var(--text-grey);
  }
  .details__ids { margin-bottom: 3px; }
  .contact { list-style: none; }
  .contact li { display: flex; align-items: center; gap: 8px; height: 20px; }
  .contact svg { width: 13px; height: 13px; flex: none; fill: var(--ink); }

  .address {
    position: absolute; right: 32px; top: 235px; text-align: right;
    font-style: normal; font-size: 14px; line-height: 18.5px; color: var(--text-grey);
  }
  .address__company { font-weight: 600; color: #3a3a3a; }

  .back-brand {
    position: absolute; left: 0; right: 0; top: 128px;
    display: flex; justify-content: center; align-items: center; gap: 16px;
  }
  .back-brand__square { width: 40px; height: 40px; background: var(--white); }
  .back-brand__name {
    font-family: "Open Sans", Arial, sans-serif; font-weight: 600;
    font-size: 50px; color: var(--white); letter-spacing: -1px;
  }
  .back-url {
    position: absolute; left: 0; right: 0; top: 295px; text-align: center;
    font-size: 14px; letter-spacing: 3px; color: var(--white);
  }
</style>
</head>
<body>
<main class="canvas">
  <section class="card card--front" aria-label="Card front">
    <div class="brand">
      <span class="brand__square"></span>
      <span class="brand__name">Harbor Builders</span>
    </div>

    <h1 class="holder">DANIEL MORROW</h1>
    <div class="rule"></div>

    <div class="details">
      <p class="details__ids">Registration 40418<br>ABN: 12 345 678 901</p>
      <ul class="contact">
        <li>
          <svg viewBox="0 0 13 13" aria-hidden="true"><path d="M3 0h7v13H3z M4.3 1.3v9h4.4v-9z M5.8 11h1.4v1.2H5.8z" fill-rule="evenodd"/></svg>
          0400 123 987
        </li>
        <li>
          <svg viewBox="0 0 13 13" aria-hidden="true"><path d="M0.5 3h12v8h-12z M1.5 4.2v0.3l5 3.3 5-3.3v-0.3z M1.5 5.7v4.3h10V5.7l-5 3.3z" fill-rule="evenodd"/></svg>
          daniel@harborbuilders.com.au
        </li>
        <li>
          <svg viewBox="0 0 13 13" aria-hidden="true"><circle cx="6.5" cy="6.5" r="6"/></svg>
          www.harborbuilders.com.au
        </li>
      </ul>
    </div>

    <address class="address">
      <span class="address__company">Harbor Builders Pty Ltd</span><br>
      PO Box 7720<br>
      Northgate<br>
      LPO Riverton WA 6148
    </address>
  </section>

  <section class="card card--back" aria-label="Card back">
    <div class="back-brand">
      <span class="back-brand__square"></span>
      <span class="back-brand__name">Harbor Builders</span>
    </div>
    <p class="back-url">www.harborbuilders.com.au</p>
  </section>
</main>
</body>
</html>
```